Webdesign für Bedrucken Papiertaschen, Schildern etc.
Zielgruppe
Wir bedrucken Papiertaschen, Papierbeutel, Laternen, Aluplaketten, Schilder, etc. und lasern Hundemarken. Zielgruppen von Privat bis Geschäftskunden
Aufgabenstellung
Der Shop sollte ein einfacher und kostengünstiger 'web2print'-shop werden. Wo die Kunden anhand von einem Editor Ihre Logos oder Druckvorlagen selber hochladen und/oder gestalten könne. Bisher haben die Kunden eifach ihre Bidldatei per E-Mail geschickt und wir haben diese dann weiter verarbeit.
Der Shop sollte, wenn möglich, günstig im Unterhalt sein, da wir nicht abschätzen können, wie gut diese laufen wird.
Wir haben wie 3 Bereich: 1. Papierbeutel/Taschen / 2. Stallplaketten (für z.B. Pferdesport) / 3. Diverses (Wie z.B. die Laternen, Schilder, Hundemarken, etc.)
Es würde sich um eine separate Webseite handeln. Daher ist bei Design freie Hand, eifach und klar... auch für nicht so ambitionierte Privatkunden oder kleine Unternehmen.

```html
<!DOCTYPE html>
<html lang="de">
<head>
<meta charset="utf-8">
<title>Tütenwerk – Web2Print Shop</title>
<link href="https://fonts.googleapis.com/css2?family=Inter:wght@400;500;600;700;800&display=swap" rel="stylesheet">
<style>
:root{
  --ink:#111;
  --heading:#3a4150;
  --text:#444b57;
  --blue:#1a9be8;
  --grey:#ebebec;
  --line:#e3e3e5;
  --black:#000;
  --white:#fff;
}
*{box-sizing:border-box;margin:0;padding:0}
html,body{width:1200px;height:2241px;overflow:hidden;background:var(--white);font-family:"Inter",sans-serif;color:var(--ink)}
.page{position:relative;width:1200px;height:2241px}
a{color:inherit;text-decoration:none}

/* header */
.site-header{position:absolute;left:44px;top:0;width:1108px;height:86px;background:var(--white);border-radius:0 0 14px 14px;box-shadow:0 4px 18px rgba(0,0,0,.08);display:flex;align-items:center;padding:0 20px 0 22px;z-index:5}
.brand{font-weight:800;font-size:22px;letter-spacing:-.5px;display:flex;align-items:center;gap:8px;width:126px}
.brand-dot{width:12px;height:12px;background:var(--black)}
.main-nav{display:flex;gap:37px;font-size:12.5px;color:#222;margin-left:24px}
.main-nav a.active{text-decoration:underline;text-underline-offset:3px}
.header-icons{margin-left:auto;display:flex;gap:13px}
.icon-btn{width:45px;height:46px;border:1px solid var(--line);border-radius:7px;display:flex;align-items:center;justify-content:center}
.icon-btn.cart{background:var(--black);border-color:var(--black)}

/* hero */
.hero{position:absolute;left:0;top:0;width:1200px;height:595px;overflow:hidden;background:linear-gradient(90deg,#f4f2f0 0%,#e9e6e3 40%,#ddd6cf 100%)}
.hero-photo{position:absolute;right:0;top:0;width:660px;height:595px;background:linear-gradient(110deg,rgba(230,40,70,.0) 0%,#e0354f 22%,#39c3cf 40%,#b7d62c 55%,#a5c02a 70%,#9a1f1f 88%,#d8c9bd 100%);opacity:.9}
.hero-content{position:absolute;left:66px;top:193px}
.eyebrow{font-size:11px;font-weight:600;letter-spacing:2.2px;text-transform:uppercase;color:var(--ink)}
.hero h1{font-size:53px;font-weight:700;line-height:63px;letter-spacing:-.8px;margin-top:21px}
.hero p{font-size:15px;line-height:25px;color:#222;margin-top:27px;width:420px}
.hero-actions{display:flex;gap:13px;margin-top:17px}
.btn{display:inline-flex;align-items:center;justify-content:center;border-radius:4px;font-size:13.5px;font-weight:500}
.btn-primary{background:var(--blue);color:var(--white)}
.btn-outline{border:1.5px solid var(--ink);color:var(--ink)}
.hero .btn-primary{width:182px;height:43px}
.hero .btn-outline{width:157px;height:43px}

/* section heads */
.section-head h2{font-size:31px;font-weight:700;color:var(--heading);letter-spacing:-.3px;margin-top:14px}
.section-head .sub{font-size:14.5px;color:var(--text);margin-top:12px}

/* categories */
.categories{position:absolute;left:0;top:595px;width:1200px;height:498px;padding:42px 66px 0}
.cat-grid{display:flex;gap:35px;margin-top:21px}
.cat-card{width:332px;height:283px;border:1px solid var(--line);border-top:4px solid var(--heading);border-radius:8px;padding:26px 26px 0;box-shadow:0 2px 6px rgba(0,0,0,.04)}
.cat-top{display:flex;align-items:center;gap:20px}
.round-icon{width:66px;height:66px;border-radius:50%;background:#1c1f24;display:flex;align-items:center;justify-content:center}
.pill{background:#ececec;border-radius:11px;font-size:10px;padding:5px 9px;color:#333}
.cat-card h3{font-size:19px;font-weight:600;color:var(--heading);margin-top:22px}
.cat-card p{font-size:11.3px;line-height:18px;color:#444;margin-top:11px;height:36px}
.cat-card .btn{width:145px;height:36px;font-size:12px;margin-top:34px}

/* steps */
.steps{position:absolute;left:0;top:1093px;width:1200px;height:345px;background:var(--grey);padding:45px 66px 0}
.step-grid{display:flex;gap:20px;margin-top:19px}
.step{width:344px}
.step-top{display:flex;align-items:center;position:relative}
.step .round-icon{width:66px;height:66px}
.step-num{position:absolute;left:52px;top:-6px;width:26px;height:26px;border-radius:50%;background:var(--white);font-size:16px;display:flex;align-items:center;justify-content:center}
.step-line{flex:1;height:2px;background:var(--heading);margin-left:14px}
.step h3{font-size:19px;font-weight:600;color:var(--heading);margin-top:25px}
.step p{font-size:15px;line-height:25px;color:var(--text);margin-top:6px;width:300px}

/* products */
.products{position:absolute;left:0;top:1438px;width:1200px;height:505px;padding:56px 66px 0}
.products .section-head h2{margin-top:0}
.prod-grid{display:flex;gap:32px;margin-top:14px}
.prod-card{width:240px;height:285px;border:1px solid var(--line);border-radius:6px;padding:8px;position:relative}
.prod-img{height:140px;border-radius:6px;background:radial-gradient(ellipse at center,#b88a52 0 26%,#111 27%)}
.prod-tag{display:inline-block;background:#ececec;border-radius:10px;font-size:9.5px;padding:4px 9px;color:#333;margin-top:20px}
.prod-card h3{font-size:13.5px;font-weight:600;color:var(--heading);line-height:16px;margin-top:12px;width:210px}
.add-btn{position:absolute;right:9px;bottom:11px;width:33px;height:33px;border-radius:5px;background:var(--blue);display:flex;align-items:center;justify-content:center}

/* footer */
.site-footer{position:absolute;left:0;top:1943px;width:1200px;height:298px;background:var(--black);color:var(--white);padding:0 66px}
.footer-brand{position:absolute;left:66px;top:52px;font-size:30px;font-weight:800;display:flex;align-items:center;gap:10px}
.footer-brand .brand-dot{background:var(--white);width:14px;height:14px}
.address{position:absolute;left:256px;top:46px;font-size:15px;line-height:25px}
.address strong{font-weight:600}
.contact-row{display:flex;align-items:center;gap:5px;margin-top:13px;font-weight:600}
.contact-chip{background:var(--white);color:var(--ink);border-radius:15px;padding:4px 11px;font-weight:400}
.legal{position:absolute;left:617px;top:70px;display:flex;flex-direction:column;gap:10px;font-size:15px}
.legal a{text-decoration:underline;text-underline-offset:3px}
.cert{position:absolute;left:997px;top:76px;width:130px;height:130px;border-radius:50%;background:var(--white)}
.copyright{position:absolute;left:66px;top:261px;font-size:15px}
</style>
</head>
<body>
<div class="page">

  <section class="hero">
    <div class="hero-photo" role="img" aria-label="Foto: Hand hält bunte Papiertragtaschen in Rot, Türkis, Grün und Dunkelrot"></div>
    <div class="hero-content">
      <div class="eyebrow">Web2Print Shop</div>
      <h1>Ihre Marke.<br>Perfekt gedruckt.</h1>
      <p>Gestalten Sie individuelle Papierbeutel, Stallplaketten und Werbemittel – einfach online, direkt druckfertig.</p>
      <div class="hero-actions">
        <a class="btn btn-primary" href="#">Jetzt gestalten →</a>
        <a class="btn btn-outline" href="#">Alle Produkte</a>
      </div>
    </div>
  </section>

  <header class="site-header">
    <div class="brand"><span class="brand-dot"></span>Tütenwerk</div>
    <nav class="main-nav">
      <a class="active" href="#">Produkte</a><a href="#">Sonderanfertigung</a><a href="#">Aktionen</a><a href="#">Materialien</a><a href="#">Nachhaltigkeit</a><a href="#">Über uns</a><a href="#">Kontakt</a>
    </nav>
    <div class="header-icons">
      <span class="icon-btn"><svg width="20" height="20" viewBox="0 0 24 24" fill="none" stroke="#111" stroke-width="1.6"><circle cx="12" cy="8" r="4"/><path d="M4 21c1-4 4-6 8-6s7 2 8 6"/></svg></span>
      <span class="icon-btn"><svg width="20" height="20" viewBox="0 0 24 24" fill="none" stroke="#111" stroke-width="1.6"><path d="M12 20s-8-5-8-11a4 4 0 0 1 8-1 4 4 0 0 1 8 1c0 6-8 11-8 11z"/></svg></span>
      <span class="icon-btn"><svg width="20" height="20" viewBox="0 0 24 24" fill="none" stroke="#111" stroke-width="1.6"><circle cx="11" cy="11" r="7"/><path d="M16 16l5 5"/></svg></span>
      <span class="icon-btn cart"><svg width="20" height="20" viewBox="0 0 24 24" fill="none" stroke="#fff" stroke-width="1.6"><path d="M3 9h18l-2 11H5z"/><path d="M8 9l4-5 4 5M9 13v4M12 13v4M15 13v4"/></svg></span>
    </div>
  </header>

  <section class="categories">
    <div class="section-head">
      <div class="eyebrow">Kategorien</div>
      <h2>Was möchten Sie gestalten?</h2>
      <div class="sub">Wählen Sie Ihre Kategorie und starten Sie direkt mit dem Design</div>
    </div>
    <div class="cat-grid">
      <article class="cat-card">
        <div class="cat-top"><span class="round-icon"><svg width="28" height="28" viewBox="0 0 24 24" fill="none" stroke="#fff" stroke-width="1.5"><rect x="4" y="4" width="16" height="16" rx="3"/><path d="M9 4v3a3 3 0 0 0 6 0V4"/></svg></span><span class="pill">45+ Produkte</span></div>
        <h3>Papierbeutel &amp; Taschen</h3>
        <p>Tragetaschen, Papierbeutel, Flachbeutel mit Ihrem Logo – in vielen Formaten und Materialien.</p>
        <a class="btn btn-primary" href="#">Jetzt entdecken →</a>
      </article>
      <article class="cat-card">
        <div class="cat-top"><span class="round-icon"><svg width="28" height="28" viewBox="0 0 24 24" fill="none" stroke="#fff" stroke-width="1.5"><path d="M7 4h10v5a5 5 0 0 1-10 0z"/><path d="M7 6H4a3 3 0 0 0 3 4M17 6h3a3 3 0 0 1-3 4M12 14v4M8 20h8"/></svg></span><span class="pill">25+ Produkte</span></div>
        <h3>Stahlplaketten</h3>
        <p>Individuell gravierte Plaketten für Pferdesport, Turniere und Vereinsauszeichnungen.</p>
        <a class="btn btn-primary" href="#">Jetzt entdecken →</a>
      </article>
      <article class="cat-card">
        <div class="cat-top"><span class="round-icon"><svg width="28" height="28" viewBox="0 0 24 24" fill="none" stroke="#fff" stroke-width="1.5"><path d="M7 9h10l1 11H6z"/><path d="M9 9V6a3 3 0 0 1 6 0v3"/></svg></span><span class="pill">45+ Produkte</span></div>
        <h3>Diverses</h3>
        <p>Laternen, Schilder, Hundemarken, Schlüsselanhänger und viele weitere Werbeartikel.</p>
        <a class="btn btn-primary" href="#">Jetzt entdecken →</a>
      </article>
    </div>
  </section>

  <section class="steps">
    <div class="section-head">
      <div class="eyebrow">So funktioniert's</div>
      <h2>In 3 Schritten zum fertigen Druckprodukt</h2>
    </div>
    <div class="step-grid">
      <div class="step">
        <div class="step-top"><span class="round-icon"><svg width="28" height="28" viewBox="0 0 24 24" fill="none" stroke="#fff" stroke-width="1.5"><rect x="4" y="4" width="16" height="16" rx="3"/><path d="M9 4v3a3 3 0 0 0 6 0V4"/></svg></span><span class="step-num">1</span><span class="step-line"></span></div>
        <h3>Produkt wählen</h3>
        <p>Wählen Sie aus über 120 Produkten das passende für Ihren Bedarf.</p>
      </div>
      <div class="step">
        <div class="step-top"><span class="round-icon"><svg width="28" height="28" viewBox="0 0 24 24" fill="none" stroke="#fff" stroke-width="1.5"><path d="M8 13a5 5 0 1 1 8 0l-1 3H9z"/><path d="M10 19h4M12 3V1M4 9H2M22 9h-2M5 4l1 1M19 4l-1 1"/></svg></span><span class="step-num">2</span><span class="step-line"></span></div>
        <h3>Motiv gestalten</h3>
        <p>Laden Sie Ihr Logo hoch oder nutzen Sie unseren Editor für individuelle Designs.</p>
      </div>
      <div class="step">
        <div class="step-top"><span class="round-icon"><svg width="28" height="28" viewBox="0 0 24 24" fill="none" stroke="#fff" stroke-width="1.5"><path d="M12 3l8 4v9l-8 5-8-5V7z"/><path d="M4 7l8 4 8-4M12 11v10"/><path d="M14 17l2 2 4-4"/></svg></span><span class="step-num">3</span><span class="step-line"></span></div>
        <h3>Bestellen &amp; liefern</h3>
        <p>Bestellung abschicken und Ihr fertiges Produkt kommt direkt zu Ihnen.</p>
      </div>
    </div>
  </section>

  <section class="products">
    <div class="section-head">
      <h2>Beliebte Produkte</h2>
      <div class="sub">Unsere meistbestellten Artikel</div>
    </div>
    <div class="prod-grid">
      <article class="prod-card"><div class="prod-img" role="img" aria-label="Produktfoto: braune Papiertragtasche mit Druck auf schwarzem Grund"></div><span class="prod-tag">Papierbeutel &amp; Taschen</span><h3>Papiertaschen braun (2-seitig bedruckt)</h3><span class="add-btn"><svg width="16" height="16" viewBox="0 0 16 16" stroke="#fff" stroke-width="2"><path d="M8 2v12M2 8h12"/></svg></span></article>
      <article class="prod-card"><div class="prod-img" role="img" aria-label="Produktfoto: braune Papiertragtasche mit Druck auf schwarzem Grund"></div><span class="prod-tag">Papierbeutel &amp; Taschen</span><h3>Papiertaschen braun (2-seitig bedruckt)</h3><span class="add-btn"><svg width="16" height="16" viewBox="0 0 16 16" stroke="#fff" stroke-width="2"><path d="M8 2v12M2 8h12"/></svg></span></article>
      <article class="prod-card"><div class="prod-img" role="img" aria-label="Produktfoto: braune Papiertragtasche mit Druck auf schwarzem Grund"></div><span class="prod-tag">Papierbeutel &amp; Taschen</span><h3>Papiertaschen braun (2-seitig bedruckt)</h3><span class="add-btn"><svg width="16" height="16" viewBox="0 0 16 16" stroke="#fff" stroke-width="2"><path d="M8 2v12M2 8h12"/></svg></span></article>
      <article class="prod-card"><div class="prod-img" role="img" aria-label="Produktfoto: braune Papiertragtasche mit Druck auf schwarzem Grund"></div><span class="prod-tag">Papierbeutel &amp; Taschen</span><h3>Papiertaschen braun (2-seitig bedruckt)</h3><span class="add-btn"><svg width="16" height="16" viewBox="0 0 16 16" stroke="#fff" stroke-width="2"><path d="M8 2v12M2 8h12"/></svg></span></article>
    </div>
  </section>

  <footer class="site-footer">
    <div class="footer-brand"><span class="brand-dot"></span>Tütenwerk</div>
    <div class="address">
      <strong>Brenner Druck AG</strong><br>Werkgasse 14<br>CH-8199 Seefeld / Zürich
      <div class="contact-row">T: <span class="contact-chip">044 555 01 23</span></div>
      <div class="contact-row">E: <span class="contact-chip">info@brenner-druck.ch</span></div>
    </div>
    <nav class="legal">
      <a href="#">Versandbedingungen</a><a href="#">Allgemeine Geschäftsbedingungen</a><a href="#">Widerrufsrecht</a><a href="#">Datenschutz</a><a href="#">Impressum</a>
    </nav>
    <div class="cert" role="img" aria-label="Zertifikatssiegel Managementsystem"></div>
    <div class="copyright">© Brenner Druck AG 2026</div>
  </footer>

</div>
</body>
</html>
```